Corporate Reception Invite (Bluebird Gathering: Amberglow Night)

I am looking for an invitation to use in Constant Contact for an upcoming reception. I have attached the company logo and a hero image from the reception location that may work well. Lastly, I attached an example from last year's invite for reference. Event details:

Bluebird Gathering: Amberglow Night @ RVQ
October 23rd, 2023 from 6:00 - 8:00 pm
Solmera at The Brisbury, Chicago
1472 W Fenwick St, Chicago, IL 60654
Join PBH & Friends for Cocktails & Conversation
Super casual - come and go as you please. Guests welcome.

Target Market(s)

Corporate audience

Font styles to use
Serif
Script
Other font styles liked:
• No strong preference, but want something elegant, sexy, and corporate

Colors
0054AA
0677BA
7BADD7
CADEEF
E8F1F8

Requirements
Must have
• PBH logo, event details, size: 600 x 1500 pixels

```html
<!DOCTYPE html>
<html lang="en">
<head>
<meta charset="utf-8">
<title>Bluebird Gathering: Amberglow Night – Invitation</title>
<link rel="stylesheet" href="https://fonts.googleapis.com/css2?family=Poppins:wght@400;500;600;700&display=swap">
<style>
  :root {
    --page: #dedede;
    --navy: #0f2a5e;
    --navy-deep: #0b2150;
    --cyan: #41c4ff;
    --sky: #7badd7;
    --mid: #0677ba;
    --royal: #0054aa;
    --ink: #1a1a1a;
    --white: #ffffff;
    --rule: rgba(64, 150, 230, 0.45);
  }
  * { box-sizing: border-box; margin: 0; padding: 0; }
  html, body {
    width: 1200px; height: 1200px; overflow: hidden;
    background: var(--page);
    font-family: "Poppins", sans-serif;
  }
  .invite {
    position: absolute; left: 77px; top: 233px;
    width: 1048px; height: 733px;
    background: var(--white);
    overflow: hidden;
  }
  .hero {
    position: absolute; left: 0; top: 0; width: 1048px; height: 504px;
    background: linear-gradient(90deg, var(--navy-deep) 0%, var(--navy) 55%, #123a7a 100%);
    overflow: hidden;
  }
  .hero-photo {
    position: absolute; right: 0; top: 0; width: 520px; height: 504px;
    background:
      radial-gradient(ellipse at 62% 55%, rgba(40,150,230,0.85) 0%, rgba(20,90,180,0.55) 35%, rgba(15,42,94,0) 75%),
      linear-gradient(180deg, #0a1d44 0%, #0d3c80 60%, #0a2a5a 100%);
    -webkit-mask-image: linear-gradient(90deg, transparent 0%, #000 40%);
            mask-image: linear-gradient(90deg, transparent 0%, #000 40%);
  }
  .title {
    position: absolute; left: 50px; top: 66px;
    color: var(--cyan); font-weight: 700; font-size: 51px; line-height: 1;
    letter-spacing: 0.2px; text-transform: uppercase; white-space: nowrap;
  }
  .subtitle {
    position: absolute; left: 50px; top: 134px;
    color: var(--white); font-weight: 600; font-size: 50px; line-height: 1; white-space: nowrap;
  }
  .rule {
    position: absolute; left: 36px; width: 700px; height: 1px;
    background: linear-gradient(90deg, transparent, var(--rule) 10%, var(--rule) 85%, transparent);
  }
  .rule-1 { top: 207px; }
  .rule-2 { top: 360px; }
  .rule-3 { top: 461px; }
  .date-icon { position: absolute; left: 55px; top: 231px; width: 108px; height: 106px; }
  .date {
    position: absolute; left: 178px; top: 226px;
    color: var(--white); font-weight: 700; font-size: 44px; line-height: 1; white-space: nowrap;
  }
  .date sup { font-size: 22px; vertical-align: 20px; }
  .date .year { font-weight: 400; }
  .time-band {
    position: absolute; left: 178px; top: 282px; width: 428px; height: 48px;
    background: var(--mid);
    clip-path: polygon(0 0, 96% 0, 100% 50%, 96% 100%, 0 100%);
    color: var(--white); font-size: 31px; line-height: 48px; padding-left: 40px; white-space: nowrap;
  }
  .time-band strong { font-weight: 700; }
  .dress {
    position: absolute; left: 55px; top: 380px;
    color: var(--sky); font-weight: 700; font-size: 25px; line-height: 1;
  }
  .note {
    position: absolute; left: 55px; top: 410px;
    color: var(--white); font-weight: 500; font-size: 27px; line-height: 1.1; white-space: nowrap;
  }
  .join {
    position: absolute; left: 55px; top: 546px;
    color: var(--mid); font-weight: 700; font-size: 28px; line-height: 1; white-space: nowrap;
  }
  .join .amp { font-weight: 400; }
  .join-sub {
    position: absolute; left: 55px; top: 581px;
    color: var(--ink); font-size: 21px; line-height: 1; white-space: nowrap;
  }
  .pin-icon { position: absolute; left: 376px; top: 543px; width: 60px; height: 60px; }
  .venue {
    position: absolute; left: 443px; top: 551px; color: var(--ink); white-space: nowrap;
  }
  .venue-name { font-weight: 700; font-size: 18px; line-height: 1.3; }
  .venue-address { font-size: 18px; line-height: 1.3; margin-top: 2px; }
  .rsvp {
    position: absolute; top: 632px; height: 40px; border-radius: 20px;
    font-size: 17px; line-height: 36px; text-align: center; white-space: nowrap;
  }
  .rsvp-primary {
    left: 55px; width: 229px; line-height: 40px;
    background: linear-gradient(90deg, var(--royal), #1e3f8f);
    color: var(--white); font-weight: 700;
  }
  .rsvp-yes { left: 306px; width: 232px; border: 2px solid var(--mid); color: var(--ink); font-weight: 500; }
  .rsvp-no { left: 560px; width: 232px; border: 2px solid var(--mid); color: var(--ink); font-weight: 500; }
  .brand {
    position: absolute; left: 840px; top: 580px;
    display: flex; align-items: center; gap: 14px;
  }
  .brand-square { width: 48px; height: 48px; background: var(--sky); }
  .brand-name { color: var(--navy); font-weight: 700; font-size: 58px; line-height: 1; }
</style>
</head>
<body>
  <main class="invite">
    <section class="hero">
      <div class="hero-photo" role="img" aria-label="Photo of a smoking blue cocktail in a martini glass with lemon slices and dried flowers"></div>

      <h1 class="title">Bluebird Gathering</h1>
      <p class="subtitle">Amberglow Night @ RVQ</p>
      <div class="rule rule-1"></div>

      <svg class="date-icon" viewBox="0 0 108 106" aria-hidden="true">
        <rect x="0" y="10" width="102" height="88" rx="3" fill="#0677ba"/>
        <rect x="0" y="10" width="102" height="16" fill="#0a8ad6"/>
        <g fill="#0f2a5e">
          <rect x="18" y="0" width="6" height="18" rx="3"/><rect x="38" y="0" width="6" height="18" rx="3"/>
          <rect x="58" y="0" width="6" height="18" rx="3"/><rect x="78" y="0" width="6" height="18" rx="3"/>
          <rect x="18" y="36" width="12" height="6"/><rect x="40" y="36" width="12" height="6"/><rect x="62" y="36" width="12" height="6"/>
          <rect x="18" y="52" width="12" height="6"/><rect x="40" y="52" width="12" height="6"/>
          <rect x="18" y="68" width="12" height="6"/><rect x="18" y="84" width="12" height="6"/>
        </g>
        <circle cx="80" cy="78" r="28" fill="#0f2a5e"/>
        <circle cx="80" cy="78" r="23" fill="#ffffff"/>
        <path d="M78 64 V80 H92" stroke="#0f2a5e" stroke-width="5" fill="none" stroke-linecap="round"/>
      </svg>

      <p class="date">OCTOBER 23<sup>RD</sup>, <span class="year">2023</span></p>
      <p class="time-band">FROM <strong>6:00 - 8:00 PM</strong></p>
      <div class="rule rule-2"></div>

      <p class="dress">SUPER CASUAL</p>
      <p class="note">come and go as you please. Guests welcome</p>
      <div class="rule rule-3"></div>
    </section>

    <section class="details">
      <p class="join">JOIN PBH <span class="amp">&amp;</span> FRIENDS</p>
      <p class="join-sub">for Cocktails &amp; Conversation</p>

      <svg class="pin-icon" viewBox="0 0 60 60" aria-hidden="true">
        <rect x="12" y="12" width="36" height="36" transform="rotate(45 30 30)" fill="none" stroke="#7badd7" stroke-width="4"/>
        <rect x="15" y="15" width="30" height="30" transform="rotate(45 30 30)" fill="none" stroke="#0f2a5e" stroke-width="3"/>
        <path d="M30 19 a7 7 0 0 1 7 7 c0 5 -7 12 -7 12 s-7 -7 -7 -12 a7 7 0 0 1 7 -7 z" fill="#0f2a5e"/>
        <circle cx="30" cy="26" r="2.6" fill="#ffffff"/>
      </svg>
      <div class="venue">
        <p class="venue-name">Solmera at The Brisbury, Chicago</p>
        <p class="venue-address">1472 W Fenwick St, Chicago, IL 60654</p>
      </div>

      <p class="rsvp rsvp-primary">Cheers! I'll be there</p>
      <p class="rsvp rsvp-yes">Cheers! I'll be there</p>
      <p class="rsvp rsvp-no">Sorry, I can't make it</p>

      <div class="brand">
        <span class="brand-square"></span>
        <span class="brand-name">PBH</span>
      </div>
    </section>
  </main>
</body>
</html>
```